Business Card Design for Training Business

Clear Path Coaching is a new business that delivers training and other services with a focus on topics related to mental health and wellbeing, for example, Wellmind Response Course, Resilience etc. We have a strong focus on evidence-based psychology and neuroscience. I have a logo which I will upload with the brief, so please consider colours that work well with the logo.
Target Market(s)
Adults, workplaces (particularly government and not-for-profits)
Industry/Entity Type
Business
Contact Information for Business Card
Head Strong TrainingSamantha SellwoodDirector0438 770 850sam@headstrongtraining.com.auwww.headstrongtraining.com.au

```html
<!DOCTYPE html>
<html lang="en">
<head>
<meta charset="utf-8">
<title>Clear Path Coaching – Business Card</title>
<link rel="stylesheet" href="https://fonts.googleapis.com/css2?family=Arimo:wght@400&family=Raleway:wght@300&display=swap">
<style>
  :root {
    --page-bg: #e6e4e1;
    --card-black: #0b0b0c;
    --band-grey: #2d2b2c;
    --teal: #3cb6be;
    --teal-deep: #2ea6ae;
    --ink: #101214;
    --brand-grey: #5a5a5c;
    --logo-teal: #4cc3c9;
  }
  * { box-sizing: border-box; margin: 0; padding: 0; }
  html, body { width: 1200px; height: 892px; overflow: hidden; }
  body {
    background: var(--page-bg);
    display: flex;
    align-items: center;
    justify-content: center;
    font-family: "Arimo", Arial, sans-serif;
  }
  .business-card {
    position: relative;
    width: 900px;
    height: 514px;
    border-radius: 28px;
    overflow: hidden;
    background: var(--card-black);
    box-shadow: 0 14px 34px rgba(0,0,0,.25);
  }
  .card-waves { position: absolute; inset: 0; width: 100%; height: 100%; }
  .brand {
    position: absolute;
    top: 44px;
    left: 420px;
    width: 420px;
    display: flex;
    flex-direction: column;
    align-items: center;
    gap: 26px;
  }
  .brand-mark {
    width: 128px;
    height: 128px;
    border-radius: 50%;
    border: 3px solid var(--logo-teal);
  }
  .brand-name {
    font-family: "Raleway", "Helvetica Neue", sans-serif;
    font-weight: 300;
    font-size: 36px;
    letter-spacing: 6px;
    color: var(--brand-grey);
    white-space: nowrap;
  }
  .person {
    position: absolute;
    top: 322px;
    right: 432px;
    text-align: right;
    color: var(--ink);
  }
  .person-name { font-size: 39px; line-height: 1.05; white-space: nowrap; }
  .person-role { font-size: 31px; line-height: 1.05; }
  .divider {
    position: absolute;
    left: 490px;
    top: 350px;
    width: 2px;
    height: 112px;
    background: var(--ink);
    transform: rotate(8deg);
  }
  .contact-list {
    position: absolute;
    top: 352px;
    left: 515px;
    list-style: none;
    color: var(--ink);
    font-size: 21px;
  }
  .contact-item {
    display: flex;
    align-items: center;
    gap: 10px;
    height: 34px;
    white-space: nowrap;
  }
  .contact-icon { width: 22px; height: 20px; flex: none; }
</style>
</head>
<body>
  <article class="business-card">
    <svg class="card-waves" viewBox="0 0 900 514" preserveAspectRatio="none" aria-hidden="true">
      <path d="M0,220 C200,170 420,235 620,278 C760,308 850,318 900,318 L900,514 L0,514 Z" fill="var(--band-grey)"/>
      <path d="M0,268 C210,228 430,290 630,328 C770,352 860,358 900,360 L900,514 L0,514 Z" fill="var(--teal)"/>
      <path d="M0,470 L900,470 L900,514 L0,514 Z" fill="var(--teal-deep)" opacity=".35"/>
    </svg>

    <header class="brand">
      <span class="brand-mark"></span>
      <span class="brand-name">CLEAR PATH COACHING</span>
    </header>

    <div class="person">
      <p class="person-name">Rebecca Tanfield</p>
      <p class="person-role">Director</p>
    </div>

    <span class="divider"></span>

    <ul class="contact-list">
      <li class="contact-item">
        <svg class="contact-icon" viewBox="0 0 22 20" aria-hidden="true">
          <rect x="1" y="1" width="20" height="18" rx="3" fill="var(--ink)"/>
          <path d="M5,7 Q11,2 17,7 L15,9 Q11,6 7,9 Z" fill="var(--teal)"/>
          <rect x="7" y="10" width="8" height="6" rx="1" fill="var(--teal)"/>
        </svg>
        <span>0491 362 517</span>
      </li>
      <li class="contact-item">
        <svg class="contact-icon" viewBox="0 0 22 20" aria-hidden="true">
          <rect x="1" y="1" width="20" height="18" rx="3" fill="var(--ink)"/>
          <rect x="5" y="6" width="12" height="8" fill="var(--teal)"/>
          <path d="M5,6 L11,11 L17,6" fill="none" stroke="var(--ink)" stroke-width="1.4"/>
        </svg>
        <span>bec@clearpathcoaching.example.au</span>
      </li>
      <li class="contact-item">
        <svg class="contact-icon" viewBox="0 0 22 20" aria-hidden="true">
          <rect x="1" y="1" width="20" height="18" rx="3" fill="var(--ink)"/>
          <circle cx="11" cy="10" r="5.5" fill="none" stroke="var(--teal)" stroke-width="1.6"/>
          <path d="M5.5,10 H16.5 M11,4.5 Q8,10 11,15.5 M11,4.5 Q14,10 11,15.5" fill="none" stroke="var(--teal)" stroke-width="1.2"/>
        </svg>
        <span>www.clearpathcoaching.example.au</span>
      </li>
    </ul>
  </article>
</body>
</html>
```